Logistics Website Design

See website https://tqfreightglobal.com for theme and color details. Need the site to be re-done and reflect some of the designs shown in this list here: https://pixelvane.com/tags/logistics-company-website

Target Market(s)

Logistics & Transportation

Industry/Entity Type

Logistics and Supply Chain

Coding

Number of Pages Required

5+ page

Requirements
Must have
• Colors must match theme of logo. Looking for a sleek, interactive design.

```html
<!DOCTYPE html>
<html lang="en">
<head>
<meta charset="utf-8">
<title>TQ Freight Global — Delivering Strength in Every Mile</title>
<link href="https://fonts.googleapis.com/css2?family=Bebas+Neue&family=Arimo:wght@400;600;700&display=swap" rel="stylesheet">
<style>
  :root {
    --black: #000000;
    --ink: #0b0b0b;
    --panel: #242424;
    --white: #ffffff;
    --muted: #d8d8d8;
    --orange: #e4602f;
    --orange-light: #ef8a63;
    --orange-deep: #d9532a;
    --divider: #b9502c;
  }
  * { margin: 0; padding: 0; box-sizing: border-box; }
  html, body { width: 1200px; height: 3314px; overflow: hidden; background: var(--black); }
  body { position: relative; font-family: "Arimo", Helvetica, Arial, sans-serif; color: var(--white); }
  .abs { position: absolute; }
  .display { font-family: "Bebas Neue", "Arial Narrow", sans-serif; font-weight: 400; letter-spacing: 1px; }
  .rule { position: absolute; height: 3px; width: 72px; background: var(--orange); }

  /* Navigation */
  .site-nav { left: 0; top: 0; width: 1200px; height: 75px; background: var(--black); z-index: 3; }
  .brand { display: flex; align-items: center; gap: 10px; }
  .brand-dot { width: 34px; height: 34px; border-radius: 50%; background: var(--orange); }
  .brand-name { font-family: "Bebas Neue", sans-serif; font-size: 26px; color: var(--white); letter-spacing: 1px; }
  .nav-brand { left: 144px; top: 20px; }
  .nav-link { top: 27px; font-size: 15px; color: var(--white); }
  .nav-link.active { color: var(--orange); }
  .btn { display: flex; align-items: center; justify-content: center; gap: 12px; background: var(--orange); color: var(--black); font-weight: 700; border-radius: 6px; }
  .nav-cta { left: 891px; top: 14px; width: 164px; height: 46px; font-size: 15px; font-weight: 600; }

  /* Hero */
  .hero { left: 0; top: 75px; width: 1200px; height: 567px;
    background: linear-gradient(180deg, #6f6a66 0%, #a9927c 22%, #c6b29a 38%, #8f8378 52%, #6c6460 64%, #3d3b3f 78%, #2a2a2f 100%); }
  .hero-title { left: 0; width: 1200px; top: 168px; text-align: center; font-size: 72px; color: var(--white); }
  .hero-sub { left: 0; width: 1200px; top: 267px; text-align: center; font-size: 18px; }
  .hero-cta { left: 500px; top: 316px; width: 200px; height: 56px; font-size: 17px; }

  /* About */
  .about-photo { left: 141px; top: 719px; width: 523px; height: 503px; border-top-right-radius: 22px;
    background: linear-gradient(135deg, #d9e4ef 0%, #f3f5f7 40%, #a8bcd2 70%, #c7d04a 100%); }
  .about-panel { left: 599px; top: 783px; width: 470px; height: 450px; background: var(--black); border-top-left-radius: 26px; }
  .about-title { left: 638px; top: 845px; font-size: 50px; line-height: 64px; }
  .about-text { left: 638px; top: 1029px; width: 418px; font-size: 13.6px; line-height: 24.2px; text-align: justify; }
  .about-badge { left: 90px; top: 1074px; width: 154px; height: 154px; border-radius: 50%; background: var(--black);
    display: flex; align-items: center; justify-content: center; text-align: center; }
  .about-badge span { font-family: "Bebas Neue", sans-serif; font-size: 24px; line-height: 24px; color: var(--orange); width: 110px; }

  /* Services */
  .services-title { left: 143px; top: 1345px; font-size: 50px; line-height: 64px; }
  .card { position: absolute; border-radius: 13px; overflow: hidden; }
  .card-label { position: absolute; left: 0; right: 0; bottom: 26px; text-align: center; font-size: 17px; color: var(--white); }
  .card-photo::after { content: ""; position: absolute; inset: 0; background: linear-gradient(180deg, rgba(0,0,0,0) 55%, rgba(0,0,0,0.55) 100%); }
  .card-label { z-index: 1; }
  .flatbed { left: 445px; top: 1301px; width: 296px; height: 319px; background: linear-gradient(180deg, #9fb6cf 0%, #c9d3dc 35%, #e5e7ea 55%, #6c7079 80%, #3b3e45 100%); }
  .dry-van { left: 145px; top: 1638px; width: 444px; height: 318px; background: linear-gradient(160deg, #b8c4cf 0%, #c4c5bf 35%, #8a2e34 55%, #b58a3c 68%, #494c51 100%); }
  .heavy-haul { left: 611px; top: 1638px; width: 444px; height: 318px; background: linear-gradient(180deg, #c9d6e3 0%, #dfe4e8 40%, #bfc2c3 60%, #5b5e63 85%, #3f4146 100%); }
  .step-deck { left: 759px; top: 1301px; width: 296px; height: 319px; background: linear-gradient(160deg, var(--orange) 0%, var(--orange-light) 100%); text-align: center; color: var(--ink); }
  .step-deck svg { position: absolute; left: 116px; top: 30px; }
  .step-deck h3 { position: absolute; top: 96px; left: 0; right: 0; font-size: 17px; font-weight: 400; }
  .step-deck p { position: absolute; top: 133px; left: 38px; right: 38px; font-size: 13.6px; line-height: 23px; }
  .learn-more { position: absolute; top: 269px; left: 0; right: 0; font-size: 14px; font-weight: 700; }

  /* Industries */
  .section-title { left: 0; width: 1200px; text-align: center; font-size: 52px; }
  .industries-band { left: 144px; top: 2150px; width: 912px; height: 200px; border-radius: 16px;
    background: linear-gradient(90deg, var(--orange-deep) 0%, var(--orange-light) 55%, var(--orange) 100%); }
  .industry { position: absolute; top: 0; height: 200px; display: flex; flex-direction: column; align-items: center; justify-content: center; gap: 16px; color: #2a120a; font-size: 15px; }
  .industry-divider { position: absolute; top: 28px; width: 1px; height: 144px; background: var(--divider); }

  /* Contact */
  .contact-bg { left: 0; top: 2380px; width: 1200px; height: 934px; background: linear-gradient(180deg, #000 0%, #141414 40%, #1e1e1e 75%, #0d0d0d 100%); }
  .contact-sub { left: 0; width: 1200px; top: 2532px; text-align: center; font-size: 17px; }
  .field { position: absolute; background: var(--panel); border-radius: 10px; display: flex; align-items: center; gap: 6px; padding-left: 22px; font-size: 11.5px; color: var(--muted); }
  .field.message { align-items: flex-start; padding-top: 23px; }
  .field em { color: var(--orange); font-style: normal; }
  .submit { left: 512px; top: 2824px; width: 176px; height: 54px; font-size: 16px; }

  /* Footer */
  .footer-brand { left: 0; width: 1200px; top: 3040px; justify-content: center; }
  .footer-links { left: 0; width: 1200px; top: 3147px; display: flex; justify-content: center; gap: 36px; font-size: 14.5px; }
  .footer-links .sep { color: var(--white); }
  .footer-line { left: 144px; top: 3187px; width: 912px; height: 1px; background: #3a3a3a; }
  .copyright { left: 0; width: 1200px; top: 3206px; text-align: center; font-size: 13.5px; }
  .social { top: 3245px; width: 30px; height: 30px; border-radius: 50%; border: 1px solid #cfcfcf; display: flex; align-items: center; justify-content: center; }
  .social.filled { background: var(--orange); border-color: var(--orange); }
</style>
</head>
<body>

<header class="abs site-nav">
  <div class="abs brand nav-brand"><span class="brand-dot"></span><span class="brand-name">TQ Freight Global</span></div>
  <span class="abs nav-link active" style="left:389px">Home</span>
  <span class="abs nav-link" style="left:467px">About Us</span>
  <span class="abs nav-link" style="left:570px">Services</span>
  <span class="abs nav-link" style="left:666px">Industries</span>
  <span class="abs nav-link" style="left:772px">Contact Us</span>
  <a class="abs btn nav-cta">Request a Quote</a>
</header>

<section class="abs hero" role="img" aria-label="Row of red, blue and white semi trucks parked before desert mountains at dusk"></section>
<h1 class="abs display hero-title">Delivering Strength in Every Mile</h1>
<p class="abs hero-sub">Secure and reliable transportation for all your cargo needs.</p>
<a class="abs btn hero-cta">Request a Quote
  <svg width="8" height="12" viewBox="0 0 8 12"><path d="M2 2l4 4-4 4" stroke="#000" stroke-width="1.6" fill="none"/></svg></a>

<section>
  <div class="abs about-photo" role="img" aria-label="Truck driver in a white cab speaking with a worker in a hard hat and safety vest holding a clipboard"></div>
  <div class="abs about-panel"></div>
  <div class="abs about-badge"><span>TQ Freight Global</span></div>
  <h2 class="abs display about-title">Keeping Your Supply<br>Chain Moving</h2>
  <div class="rule" style="left:638px;top:990px"></div>
  <p class="abs about-text">We deliver a comprehensive range of open-deck and specialized transportation services including flatbed, step deck, heavy haul, and over-dimensional freight solutions. Backed by years of experience, a trusted nationwide carrier network, and a strong safety-first culture, we provide reliable, adaptable logistics support built around the unique requirements of every load.</p>
</section>

<section>
  <h2 class="abs display services-title">Experience<br>Our Services<br>Excellence</h2>
  <div class="rule" style="left:143px;top:1564px"></div>

  <div class="card card-photo flatbed" role="img" aria-label="White semi truck on an open road"><span class="card-label">Flatbed Transportation</span></div>
  <div class="card step-deck">
    <svg width="64" height="48" viewBox="0 0 64 48" fill="#1a0c07">
      <rect x="2" y="10" width="30" height="22" rx="2"/>
      <path d="M34 16h14l10 10v8H34z"/>
      <rect x="40" y="19" width="9" height="6" fill="#ef8a63"/>
      <rect x="0" y="34" width="62" height="3"/>
      <circle cx="12" cy="40" r="5"/><circle cx="24" cy="40" r="5"/><circle cx="50" cy="40" r="5"/>
    </svg>
    <h3>Step Deck Transportation</h3>
    <p>Our step deck trucking services support tall, heavy, and specialized freight that requires additional height clearance and flexible loading options.</p>
    <span class="learn-more">Learn More &nbsp;&nbsp;›</span>
  </div>
  <div class="card card-photo dry-van" role="img" aria-label="Red semi truck with a silver trailer beside autumn trees"><span class="card-label">Dry Van Transportation</span></div>
  <div class="card card-photo heavy-haul" role="img" aria-label="White semi truck on a highway at sunset"><span class="card-label">Heavy Haul Transportation</span></div>
</section>

<section>
  <h2 class="abs display section-title" style="top:2030px">Industries We Serve</h2>
  <div class="rule" style="left:564px;top:2114px"></div>
  <div class="abs industries-band">
    <div class="industry" style="left:0;width:207px">
      <svg width="64" height="64" viewBox="0 0 64 64" fill="none" stroke="#1a0c07" stroke-width="2.2" stroke-linecap="round">
        <ellipse cx="18" cy="16" rx="9" ry="12" transform="rotate(-45 18 16)"/>
        <path d="M25 23L58 58"/><path d="M52 4L8 58"/><path d="M46 4l-8 10M58 14l-10 8M52 8l-8 9"/>
      </svg>
      <span>Food &amp; Beverage</span>
    </div>
    <div class="industry-divider" style="left:207px"></div>
    <div class="industry" style="left:207px;width:250px">
      <svg width="64" height="64" viewBox="0 0 64 64" fill="none" stroke="#1a0c07" stroke-width="2.2" stroke-linejoin="round">
        <path d="M10 6h44l4 14H6z"/><path d="M6 20c0 5 9 5 9 0c0 5 9 5 9 0c0 5 8 5 8 0c0 5 8 5 8 0c0 5 9 5 9 0c0 5 9 5 9 0"/>
        <path d="M9 27v31h46V27"/><path d="M20 36h4l4 12h14l3-9H26"/><circle cx="30" cy="52" r="1.5"/><circle cx="40" cy="52" r="1.5"/>
      </svg>
      <span>E-commerce &amp; Retail</span>
    </div>
    <div class="industry-divider" style="left:457px"></div>
    <div class="industry" style="left:457px;width:213px">
      <svg width="68" height="64" viewBox="0 0 68 64" fill="none" stroke="#1a0c07" stroke-width="2.2">
        <circle cx="26" cy="20" r="7"/><circle cx="26" cy="20" r="14" stroke-dasharray="5 3"/>
        <rect x="40" y="32" width="10" height="10"/><rect x="50" y="38" width="8" height="8"/>
        <rect x="2" y="48" width="64" height="12" rx="6"/>
        <circle cx="12" cy="54" r="2"/><circle cx="22" cy="54" r="2"/><circle cx="32" cy="54" r="2"/><circle cx="42" cy="54" r="2"/><circle cx="52" cy="54" r="2"/>
      </svg>
      <span>Manufacturing</span>
    </div>
    <div class="industry-divider" style="left:670px"></div>
    <div class="industry" style="left:670px;width:242px">
      <svg width="68" height="64" viewBox="0 0 68 64" fill="none" stroke="#1a0c07" stroke-width="2.2" stroke-linejoin="round">
        <rect x="8" y="2" width="28" height="8" rx="1"/><path d="M6 12h32v46H6z"/>
        <path d="M18 28h8v6h6v8h-6v6h-8v-6h-6v-8h6z"/>
        <rect x="34" y="44" width="30" height="12" rx="6" transform="rotate(-20 49 50)"/>
        <circle cx="52" cy="52" r="8"/>
      </svg>
      <span>Pharma &amp; Healthcare</span>
    </div>
  </div>
</section>

<section>
  <div class="abs contact-bg"></div>
  <h2 class="abs display section-title" style="top:2417px">Contact Us</h2>
  <div class="rule" style="left:564px;top:2502px"></div>
  <p class="abs contact-sub">Let's discuss your logistics needs and how we can help your business thrive</p>

  <div class="field" style="left:192px;top:2590px;width:392px;height:54px">
    <svg width="10" height="11" viewBox="0 0 10 11" fill="#e0e0e0"><circle cx="5" cy="3" r="3"/><path d="M0 11c0-4 2-5 5-5s5 1 5 5z"/></svg>Full Name <em>*</em></div>
  <div class="field" style="left:192px;top:2657px;width:392px;height:54px">
    <svg width="11" height="11" viewBox="0 0 24 24" fill="#e0e0e0"><path d="M6.6 10.8a15 15 0 006.6 6.6l2.2-2.2c.3-.3.7-.4 1-.2 1.1.4 2.3.6 3.6.6.6 0 1 .4 1 1V20c0 .6-.4 1-1 1A17 17 0 013 4c0-.6.4-1 1-1h3.5c.6 0 1 .4 1 1 0 1.2.2 2.4.6 3.6.1.3 0 .7-.2 1z"/></svg>Phone Number <em>*</em></div>
  <div class="field" style="left:192px;top:2722px;width:392px;height:55px">
    <svg width="12" height="10" viewBox="0 0 12 10" fill="#e0e0e0"><rect width="12" height="10" rx="1"/><path d="M0 1l6 4 6-4" stroke="#242424" fill="none"/></svg>Email Address <em>*</em></div>
  <div class="field message" style="left:616px;top:2590px;width:391px;height:187px">
    <svg width="12" height="11" viewBox="0 0 12 11" fill="#e0e0e0"><ellipse cx="6" cy="5" rx="6" ry="4.5"/><path d="M2 8l-1 3 4-2z"/></svg>Message <em>*</em></div>

  <a class="abs btn submit">Submit Now
    <svg width="8" height="12" viewBox="0 0 8 12"><path d="M2 2l4 4-4 4" stroke="#000" stroke-width="1.6" fill="none"/></svg></a>
</section>

<footer>
  <div class="abs brand footer-brand"><span class="brand-dot"></span><span class="brand-name" style="font-size:32px">TQ Freight Global</span></div>
  <nav class="abs footer-links">
    <span>HOME</span><span class="sep">|</span><span>ABOUT US</span><span class="sep">|</span><span>SERVICES</span><span class="sep">|</span><span>INDUSTRIES</span><span class="sep">|</span><span>CONTACT US</span>
  </nav>
  <div class="abs footer-line"></div>
  <p class="abs copyright">© 2026 TQ Freight Global - &nbsp;All Rights Reserved</p>
  <div class="abs social filled" style="left:551px">
    <svg width="13" height="10" viewBox="0 0 12 10" fill="#111"><rect width="12" height="10" rx="1"/><path d="M0 1l6 4 6-4" stroke="#e4602f" fill="none"/></svg></div>
  <div class="abs social" style="left:587px">
    <svg width="13" height="13" viewBox="0 0 24 24" fill="none" stroke="#fff" stroke-width="2"><path d="M6.6 10.8a15 15 0 006.6 6.6l2.2-2.2c.3-.3.7-.4 1-.2 1.1.4 2.3.6 3.6.6.6 0 1 .4 1 1V20c0 .6-.4 1-1 1A17 17 0 013 4c0-.6.4-1 1-1h3.5c.6 0 1 .4 1 1 0 1.2.2 2.4.6 3.6.1.3 0 .7-.2 1z"/></svg></div>
  <div class="abs social" style="left:624px">
    <svg width="14" height="14" viewBox="0 0 24 24" fill="none" stroke="#e4602f" stroke-width="2"><circle cx="12" cy="12" r="10"/><path d="M2 12h20M12 2c3 3 4 6 4 10s-1 7-4 10c-3-3-4-6-4-10s1-7 4-10z"/></svg></div>
</footer>

</body>
</html>
```